Brell Stone Company Business Cards

Front and Back Business Card - logo and text setup - cool design. I need workable photoshop or illustrator files so I can setup each employee card with design that is created
Updates

Hi everyone, thank you for the great entries. Please no more white and blue cards - there are so many already - black and silver only now please. thanks!

Target Market(s)

Construction Industry - Facility Managers

Industry/Entity Type

Construction

Contact Information for Business Card

I really like contemporary simplistic looks - clean neat....not opposed to seeing some black backrounds

Requirements
Must have
• Logo/website address with design on front only - www.brellstone-example.com (logo attached)
• Back:
• Name/Title/Company Address/Phone/email address
Nice to have
• Cool design
Should not have
• Nothing gimmicky like Fire or Water - since we are a Fire Protection company - it has all been done

```html
<!DOCTYPE html>
<html lang="en">
<head>
<meta charset="utf-8">
<title>Brell Stone Company Business Cards</title>
<link href="https://fonts.googleapis.com/css2?family=Lato:wght@400;700;900&display=swap" rel="stylesheet">
<style>
  :root {
    --page-bg: #1c1c1c;
    --card-bg: #121212;
    --silver: #b5b5b5;
    --silver-bright: #d6d6d6;
    --text-light: #cfcfcf;
    --text-muted: #9a9a9a;
    --rule: #3a3a3a;
  }
  * { margin: 0; padding: 0; box-sizing: border-box; }
  html, body {
    width: 1200px; height: 900px; overflow: hidden;
    background: var(--page-bg);
    font-family: "Lato", sans-serif;
  }
  .stage { position: relative; width: 1200px; height: 900px; }
  .card {
    position: absolute;
    left: 290px;
    width: 620px; height: 354px;
    background: var(--card-bg);
    border-radius: 22px;
    box-shadow: 0 10px 30px rgba(0,0,0,.55);
  }
  .card--front { top: 70px; }
  .card--back { top: 476px; }

  .front-logo {
    position: absolute; left: 0; right: 0; top: 120px;
    text-align: center;
    font-weight: 900; font-size: 64px; letter-spacing: -1px;
    color: var(--silver);
  }
  .front-web {
    position: absolute; left: 0; right: 0; top: 262px;
    text-align: center;
    font-size: 15px; color: var(--text-light);
  }

  .back-logo {
    position: absolute; right: 40px; top: 46px;
    font-weight: 900; font-size: 54px; letter-spacing: -1px;
    color: var(--silver);
  }
  .back-rule {
    position: absolute; left: 250px; right: 40px; top: 150px;
    height: 1px; background: var(--rule);
  }
  .person { position: absolute; left: 44px; top: 170px; }
  .person__name {
    font-size: 22px; font-weight: 400; letter-spacing: .5px;
    color: var(--silver-bright); text-transform: uppercase;
  }
  .person__title { font-size: 17px; color: var(--text-muted); margin-top: 2px; }
  .contact { list-style: none; margin-top: 16px; }
  .contact__item {
    display: flex; align-items: center; gap: 10px;
    font-size: 17px; color: var(--text-light); line-height: 26px;
  }
  .contact__icon { width: 14px; height: 14px; fill: var(--silver); flex: none; }
  .address {
    position: absolute; right: 40px; top: 176px;
    text-align: right; font-size: 16px; line-height: 22px;
    font-style: normal;
    color: var(--text-light);
  }
</style>
</head>
<body>
<main class="stage">
  <section class="card card--front" aria-label="Card front">
    <div class="front-logo">Brell Stone</div>
    <div class="front-web">www.brellstone-example.com</div>
  </section>

  <section class="card card--back" aria-label="Card back">
    <div class="back-logo">Brell Stone</div>
    <div class="back-rule"></div>

    <div class="person">
      <div class="person__name">Daniel Morgan</div>
      <div class="person__title">Managing Director</div>
      <ul class="contact">
        <li class="contact__item">
          <svg class="contact__icon" viewBox="0 0 16 16" aria-hidden="true"><path d="M3 1h3l1.5 4-2 1.3a9 9 0 0 0 4.2 4.2L11 8.5l4 1.5v3a2 2 0 0 1-2 2A12 12 0 0 1 1 3a2 2 0 0 1 2-2z"/></svg>
          044-555 010 220
        </li>
        <li class="contact__item">
          <svg class="contact__icon" viewBox="0 0 16 16" aria-hidden="true"><path d="M1 3h14v10H1z"/><path d="M1.5 3.8 8 9l6.5-5.2" fill="none" stroke="#121212" stroke-width="1.3"/></svg>
          info@brellstone-example.com
        </li>
        <li class="contact__item">
          <svg class="contact__icon" viewBox="0 0 16 16" aria-hidden="true"><circle cx="8" cy="8" r="7"/><path d="M1 8h14M8 1c-3 3.5-3 10.5 0 14M8 1c3 3.5 3 10.5 0 14" fill="none" stroke="#121212" stroke-width="1"/></svg>
          www.brellstone-example.com
        </li>
      </ul>
    </div>

    <address class="address">
      421, Address line here<br>
      Country Name, 45452
    </address>
  </section>
</main>
</body>
</html>
```